Bright Pelvicare Business Card

Need a business card for a surgical practice called Bright Pelvicare. We have recently selected a logo (attached). The business card will need to have two formats:
1) One with the logo/physician name/ contact info on the front and location information on the back.
2) One in "appointment reminder card" style with the logo/ contact info/ date/ time on the front and the location information on the back.

The front side should include the following information:
- Logo
- Rohan K. Desai, MD FACOG
- phone: 469-555-0182
- fax: 1-469-555-0317
- email: admin@brightpelvi.com
- website: www.brightpelvicare.com

The back side should have the office locations listed:
4518 Kestrel Ave, Plano, TX 75198
3920 Bramwell Rd, Plano, TX 75147
2245 Silverpine Ln, Irving, TX 75163
815 W Garnet Ave S310, Dallas, TX 75284
3614 Lantern Blvd, Grand Prairie, TX 75179
7405 Amberly Crest Dr, San Antonio, TX 78391
5812 Tolliver Rd, Pasadena, TX 77639

Target Market(s)

1. Other physicians who might refer patients
2. Female patients

Industry/Entity Type

Business

Font styles to use
Other font styles liked:
• Tahoma for lettering

Requirements
Must have
• As per the instructions
Should not have
• No other images needed -- please try to keep font consistent with logo design. Can use Tahoma as the font for lettering.

```html
<!DOCTYPE html>
<html lang="en">
<head>
<meta charset="utf-8">
<title>Bright Pelvicare Business Card</title>
<link rel="stylesheet" href="https://fonts.googleapis.com/css2?family=Michroma&family=Questrial&display=swap">
<style>
  :root {
    --navy: #1c3a86;
    --navy-soft: #8d9cc8;
    --white: #ffffff;
    --brand-blue: #234a92;
    --contact-yellow: #f2e418;
    --page: #ffffff;
  }
  html, body {
    margin: 0;
    padding: 0;
    width: 1099px;
    height: 1200px;
    overflow: hidden;
    background: var(--page);
  }
  .canvas {
    position: relative;
    width: 1099px;
    height: 1200px;
  }
  .card {
    position: absolute;
    left: 140px;
    width: 820px;
    height: 542px;
    border-radius: 12px;
    overflow: hidden;
    background: linear-gradient(to bottom,
      var(--navy) 0%,
      var(--navy) 7%,
      var(--navy-soft) 25%,
      var(--white) 43%,
      var(--white) 57%,
      var(--navy-soft) 76%,
      var(--navy) 93%,
      var(--navy) 100%);
  }
  .card--front { top: 43px; }
  .card--back { top: 633px; }

  .brand {
    position: absolute;
    left: 0;
    right: 0;
    top: 214px;
    text-align: center;
    font-family: "Questrial", sans-serif;
    color: var(--brand-blue);
  }
  .brand__mark {
    display: inline-block;
    width: 20px;
    height: 20px;
    border-radius: 50%;
    background: var(--brand-blue);
    margin-right: 14px;
    vertical-align: middle;
  }
  .brand__name {
    font-size: 54px;
    line-height: 58px;
    letter-spacing: 0.5px;
    vertical-align: middle;
  }
  .brand__tagline {
    margin-top: 0;
    font-size: 40px;
    line-height: 46px;
  }

  .contact, .locations {
    position: absolute;
    left: 0;
    right: 0;
    margin: 0;
    padding: 0;
    list-style: none;
    text-align: center;
    font-family: "Michroma", sans-serif;
    font-variant: small-caps;
    color: var(--contact-yellow);
  }
  .contact {
    top: 378px;
    font-size: 14px;
    line-height: 22px;
    letter-spacing: 2.4px;
  }
  .locations {
    font-size: 13px;
    line-height: 19.5px;
    letter-spacing: 2px;
  }
  .locations--upper { top: 46px; }
  .locations--lower { top: 420px; }
</style>
</head>
<body>
<div class="canvas">
  <section class="card card--front">
    <div class="brand">
      <div><span class="brand__mark"></span><span class="brand__name">Bright Pelvicare</span></div>
      <div class="brand__tagline">care.....with.....grace</div>
    </div>
    <ul class="contact">
      <li>Rohan K. Desai, MD FACOG</li>
      <li>phone: 469-555-0182</li>
      <li>fax: 1-469-555-0317</li>
      <li>email: admin@brightpelvi.com</li>
      <li>website: www.brightpelvicare.com</li>
    </ul>
  </section>

  <section class="card card--back">
    <ul class="locations locations--upper">
      <li>4518 Kestrel Ave, Plano, TX 75198</li>
      <li>3920 Bramwell Rd, Plano, TX 75147</li>
      <li>2245 Silverpine Ln, Irving, TX 75163</li>
      <li>815 W Garnet Ave S310, Dallas, TX 75284</li>
    </ul>
    <ul class="locations locations--lower">
      <li>3614 Lantern Blvd, Grand Prairie, TX 75179</li>
      <li>7405 Amberly Crest Dr, San Antonio, TX 78391</li>
      <li>5812 Tolliver Rd, Pasadena, TX 77639</li>
    </ul>
  </section>
</div>
</body>
</html>
```